Postcard for Antique Furniture Restorer

My business is to restore antique furniture. I am based in Sydney, Australia.

I will be using this postcard to promote my business.
I will give it to customers like a With Compliments card.

Sometimes I will be writing information on the back of the card.

Design for Postcard Size eg 148 X 105mm

Front of card:

Attached are images of Antique furniture - please use ONLY 1 of the 3 images.
Deep etch the image on a white or cream background.

On front of card add these words:
Grainward Keepsakes
antique furniture restoration

Antiques travel through time, seeing generations of families
Through time they remain - they tell a continuing story
Be part of the journey

Back of postcard:
(leave space for notes to be handwritten)

Add these words:

Grainward Keepsakes
Corin Maddaford
mobile 0473 582 316
www.oakmendcraftery.com.au

Industry/Entity Type

Business

Font styles to use
Serif
Sans Serif

Colors
fefdec
ffffff

Requirements
Must have
• Use only 1 image. Image must be deep etched.

```html
<!DOCTYPE html>
<html lang="en">
<head>
<meta charset="utf-8">
<title>Grainward Keepsakes – Postcard</title>
<link rel="stylesheet" href="https://fonts.googleapis.com/css2?family=Philosopher:wght@700&family=Crimson+Text:ital,wght@0,400;0,700;1,400&display=swap">
<style>
  :root {
    --backdrop: #8a8a8a;
    --ink-brown: #5b2812;
    --ink-soft: #6a3a22;
    --parchment-light: #f1e6cb;
    --parchment-mid: #dcc69c;
    --parchment-dark: #b89868;
    --cream: #f3ebdd;
    --cream-edge: #e7dcc8;
    --flourish: rgba(255, 250, 240, 0.55);
    --wood-dark: #4a1c10;
    --wood-mid: #8a3420;
    --wood-light: #b5583a;
  }
  * { box-sizing: border-box; margin: 0; padding: 0; }
  html, body {
    width: 1200px; height: 530px; overflow: hidden;
    background: var(--backdrop);
  }
  .stage { position: relative; width: 1200px; height: 530px; }

  .card { position: absolute; top: 66px; width: 548px; height: 394px; }

  /* Front */
  .card--front { left: 42px; }
  .front-sheet {
    position: absolute; inset: 0;
    background: radial-gradient(ellipse at 40% 40%, var(--parchment-light), var(--parchment-mid) 70%, var(--parchment-dark));
    clip-path: polygon(0 0, 100% 0, 100% 88%, 94% 90%, 88% 87%, 80% 91%, 72% 88%, 64% 92%, 55% 89%, 46% 93%, 37% 89%, 28% 92%, 19% 88%, 10% 92%, 4% 89%, 0 91%);
  }
  .front-flourish {
    position: absolute; left: 150px; top: 40px; width: 170px; height: 300px;
    background: radial-gradient(ellipse, var(--flourish), transparent 70%);
  }
  .furniture-photo {
    position: absolute; left: 298px; top: 28px; width: 218px; height: 320px;
    background: linear-gradient(90deg, var(--wood-dark), var(--wood-mid) 30%, var(--wood-light) 55%, var(--wood-mid) 80%, var(--wood-dark));
    border-radius: 4px 4px 2px 2px;
  }
  .front-copy {
    position: absolute; left: 20px; top: 68px; width: 272px;
    text-align: center; color: var(--ink-brown);
  }

  .brand-name {
    font-family: "Philosopher", sans-serif; font-weight: 700;
    font-size: 22px; line-height: 1.1;
  }
  .brand-line {
    font-family: "Philosopher", sans-serif; font-weight: 700;
    font-size: 17px; margin-top: 4px;
  }
  .tagline {
    font-family: "Crimson Text", serif; font-style: italic;
    font-size: 15px; line-height: 19px; margin-top: 22px; color: var(--ink-soft);
  }
  .tagline-close {
    font-family: "Crimson Text", serif; font-size: 15px; margin-top: 3px; color: var(--ink-brown);
  }

  /* Back */
  .card--back {
    left: 617px; width: 547px; height: 397px;
    background: var(--cream);
    border: 3px solid var(--cream-edge);
  }
  .back-flourish {
    position: absolute; left: 0; width: 230px;
    background: radial-gradient(ellipse at 30% 50%, rgba(255,255,255,0.8), transparent 70%);
  }
  .back-flourish--top { top: 0; height: 130px; }
  .back-flourish--bottom { bottom: 0; height: 110px; }
  .back-copy {
    position: absolute; left: 0; top: 118px; width: 302px;
    text-align: center; color: var(--ink-brown);
  }
  .contact-name {
    font-family: "Crimson Text", serif; font-style: italic;
    font-size: 18px; margin-top: 22px; color: var(--ink-soft);
  }
  .contact-phone {
    font-family: "Crimson Text", serif; font-size: 18px; line-height: 1.2;
  }
  .contact-web {
    font-family: "Crimson Text", serif; font-weight: 700; font-size: 13px; margin-top: 2px;
  }
</style>
</head>
<body>
<main class="stage">
  <section class="card card--front" aria-label="Postcard front">
    <div class="front-sheet"></div>
    <div class="front-flourish" role="img" aria-label="Pale floral scroll ornament"></div>
    <div class="furniture-photo" role="img" aria-label="Deep-etched photo of a carved antique wooden armoire"></div>
    <div class="front-copy">
      <h1 class="brand-name">Grainward Keepsakes</h1>
      <p class="brand-line">Antique Furniture Restoration</p>
      <p class="tagline">Antiques travel through time, seeing<br>generations of families<br>Through time they remain - they tell a<br>continuing story</p>
      <p class="tagline-close">Be part of the journey</p>
    </div>
  </section>

  <section class="card card--back" aria-label="Postcard back">
    <div class="back-flourish back-flourish--top" role="img" aria-label="Pale floral scroll ornament"></div>
    <div class="back-flourish back-flourish--bottom" role="img" aria-label="Pale floral scroll ornament"></div>
    <div class="back-copy">
      <h2 class="brand-name">Grainward Keepsakes</h2>
      <p class="brand-line">Antique Furniture Restoration</p>
      <p class="contact-name">Corin Maddaford</p>
      <p class="contact-phone">0473 582 316</p>
      <p class="contact-web">www.oakmendcraftery.com.au</p>
    </div>
  </section>
</main>
</body>
</html>
```